The K7 Momentum Collective Website

We have a pitch deck and messaging drafted. Target audience is academic institutions and VC investors that have seed money in start ups.

Need a basic website

Industry/Entity Type

LIfe Science, Diagnostic, medical device.

Coding

Coded - Design and coding required

Number of Pages Required

5+ page

```html
<!DOCTYPE html>
<html lang="en">
<head>
<meta charset="utf-8">
<title>The K7 Momentum Collective</title>
<link href="https://fonts.googleapis.com/css2?family=Poppins:wght@300;400;500;600;700&family=Source+Sans+3:wght@300;400;600;700&display=swap" rel="stylesheet">
<style>
:root{
  --teal:#4fb3c8;
  --teal-band:#5bb8cc;
  --teal-soft:#bfe4ea;
  --ink:#111;
  --body:#333;
  --grey-bg:#eeeff0;
  --footer:#000;
  --white:#fff;
}
*{margin:0;padding:0;box-sizing:border-box}
html,body{width:1200px;height:3310px;overflow:hidden;background:var(--white)}
body{position:relative;font-family:"Source Sans 3",sans-serif;color:var(--ink)}
.abs{position:absolute}
a{color:inherit;text-decoration:none}

/* header */
.site-header{position:absolute;left:0;top:0;width:1200px;height:84px;background:var(--white)}
.brand{left:99px;top:24px;font-family:"Source Sans 3",sans-serif;font-weight:300;font-size:26px;color:#222}
.nav{top:29px;font-family:"Poppins",sans-serif;font-size:16px;color:#111}
.nav.active{color:var(--teal);font-weight:500;border-bottom:2px solid var(--teal);padding-bottom:2px}
.btn{background:var(--teal);color:var(--white);font-family:"Poppins",sans-serif;font-weight:600;display:flex;align-items:center;justify-content:center;border-radius:2px}
.btn-contact{left:958px;top:17px;width:144px;height:51px;font-size:19px}

/* hero */
.hero{left:0;top:84px;width:1200px;height:514px;background:linear-gradient(180deg,#3d4c5e 0%,#2b3543 55%,#232b36 100%)}
.hero-title{left:0;top:278px;width:1200px;text-align:center;color:var(--white);font-weight:600;font-size:60px}
.hero-title sup{font-size:34px;vertical-align:28px}
.hero-sub{left:0;top:356px;width:1200px;text-align:center;color:var(--white);font-size:25px}
.btn-start{left:542px;top:410px;width:155px;height:50px;font-size:19px}

/* about */
.h2{font-weight:700;font-size:32px;color:var(--ink)}
.about-title{left:99px;top:648px}
.about-text{left:99px;top:692px;width:485px;font-size:15px;line-height:31px;color:var(--body);text-align:justify}
.btn-more{left:97px;top:1045px;width:145px;height:50px;font-size:19px;box-shadow:2px 3px 4px rgba(0,0,0,.2)}
.about-back{left:630px;top:680px;width:454px;height:408px;background:var(--teal)}
.about-dot{left:996px;top:631px;width:132px;height:132px;border-radius:50%;background:var(--teal-soft)}
.about-photo{left:647px;top:663px;width:454px;height:408px;background:linear-gradient(135deg,#5a6470,#2e3640 60%,#1d232b)}

/* discovery */
.discovery{left:0;top:1150px;width:1200px;height:463px;background:linear-gradient(180deg,#5bb8cc,#56afc3)}
.band-title{left:0;top:1188px;width:1200px;text-align:center;color:var(--white);font-weight:600;font-size:31px}
.step-frame{width:237px;height:283px;border:3px solid var(--white);border-left:none;border-radius:0 6px 6px 0}
.step-card{width:237px;height:267px;background:var(--white);border-radius:4px;text-align:center}
.step-card svg{margin-top:28px}
.step-name{font-weight:700;font-size:21px;margin-top:6px}
.step-line{font-size:15px;line-height:31px;color:#222}
.knob{width:12px;height:12px;border:2px solid var(--white);border-radius:50%;background:var(--teal-band)}

/* solution */
.sol-title{left:79px;top:1658px}
.sol-intro{left:79px;top:1705px;width:400px;font-size:14.5px;line-height:31px;color:#222}
.sol-sub{left:79px;top:1770px;font-size:20px;font-weight:600}
.problem{left:80px;font-size:15px;color:#222;display:flex;gap:10px;line-height:31px}
.problem i{flex:none;width:16px;height:16px;border:3px solid var(--teal);border-radius:50%;margin-top:8px}
.issue{width:197px;height:177px;border:2px solid var(--teal);border-radius:4px;text-align:center;font-weight:600;font-size:21px;display:flex;flex-direction:column;align-items:center;justify-content:flex-end;padding-bottom:22px;gap:14px}

/* partners */
.partners{left:0;top:2012px;width:1200px;height:563px;background:var(--grey-bg)}
.partners-title{left:0;top:2066px;width:1200px;text-align:center;font-weight:600;font-size:31px}
.partner-photo{width:276px;height:276px;border-radius:50%}
.partner-name{width:300px;text-align:center;font-family:"Poppins",sans-serif;font-weight:600;font-size:20px}

/* funding */
.funding-title{left:0;top:2615px;width:1200px;text-align:center;font-weight:600;font-size:31px}
.fund{top:2672px;width:336px;height:274px;background:var(--teal);color:var(--white);font-weight:600}
.fund-vc{left:256px;border-radius:50px 0 0 0;padding:80px 0 0 60px}
.fund-other{left:608px;border-radius:0 50px 0 0;padding:30px 0 0 57px}
.fund h3{font-size:31px;font-weight:700;margin-bottom:4px}
.fund p{font-size:20px;line-height:34.5px}

/* footer */
.site-footer{left:0;top:3005px;width:1200px;height:305px;background:var(--footer);color:var(--white)}
.foot-brand{left:0;top:3044px;width:1200px;text-align:center;font-weight:300;font-size:26px}
.foot-nav{left:0;top:3109px;width:1200px;display:flex;justify-content:center;gap:36px;font-size:16px}
.social{top:3162px;width:33px;height:33px;border:2px solid var(--white);border-radius:50%}
.copyright{left:0;top:3250px;width:1200px;text-align:center;font-size:16px;font-weight:600}
</style>
</head>
<body>

<header class="site-header">
  <div class="abs brand">The K7 Momentum Collective™</div>
  <a class="abs nav active" style="left:540px">Home</a>
  <a class="abs nav" style="left:636px">About Us</a>
  <a class="abs nav" style="left:749px">Solution</a>
  <a class="abs nav" style="left:856px">Partners</a>
  <a class="abs btn btn-contact">Contact Us</a>
</header>

<section>
  <div class="abs hero" role="img" aria-label="Photo of executives meeting around a boardroom table with city windows behind"></div>
  <h1 class="abs hero-title">The K7 Momentum Collective<sup>TM</sup></h1>
  <p class="abs hero-sub">Accelerating your innovative IP to market!</p>
  <a class="abs btn btn-start">Get Started</a>
  <svg class="abs" style="left:572px;top:522px" width="56" height="30" viewBox="0 0 56 30" fill="none" stroke-width="3" stroke-linecap="round">
    <path d="M16 4 L6 15 L16 26" stroke="rgba(255,255,255,.55)"/>
    <path d="M40 4 L50 15 L40 26" stroke="#fff"/>
  </svg>
</section>

<section>
  <h2 class="abs h2 about-title">About Us</h2>
  <div class="abs about-text">
    <p>The K7 Momentum Collective™ (K7) is a group of experienced executives whose careers have been focused on taking innovative ideas to market by strategically navigating the buildout of best-in-class life science and diagnostic organizations. This experience makes us uniquely equipped to be involved in all aspects of your due diligence on new or existing investments (business analysis, industry thesis, competitive landscape.</p>
    <p style="margin-top:31px">Business/pricing model, and financial modeling as it relates to validation of the assumptions in the model to determine the return expectations). This includes the following services:</p>
  </div>
  <a class="abs btn btn-more">Read More</a>
  <div class="abs about-dot"></div>
  <div class="abs about-back"></div>
  <div class="abs about-photo" role="img" aria-label="Photo of business people shaking hands across a meeting table"></div>
</section>

<section>
  <div class="abs discovery" role="img" aria-label="Teal-tinted photo of an office team at work"></div>
  <h2 class="abs band-title">Discovery to Market</h2>

  <div class="abs step-frame" style="left:88px;top:1258px"></div>
  <div class="abs step-frame" style="left:360px;top:1258px"></div>
  <div class="abs step-frame" style="left:631px;top:1258px"></div>
  <div class="abs step-frame" style="left:902px;top:1258px"></div>

  <div class="abs step-card" style="left:73px;top:1270px">
    <svg width="80" height="80" viewBox="0 0 80 80" fill="none" stroke="#2a6b7a" stroke-width="2.5"><circle cx="28" cy="16" r="10"/><path d="M12 42c0-10 8-16 16-16s16 6 16 16"/><circle cx="60" cy="26" r="9"/><circle cx="20" cy="62" r="11"/><path d="M36 74V60M46 74V54M56 74V48M66 74V42M40 56l12-8 10 4 12-14"/></svg>
    <div class="step-name">Discovery</div>
    <div class="step-line">Business model<br>Org structure &amp; planning<br>Cash planning</div>
  </div>
  <div class="abs step-card" style="left:345px;top:1270px">
    <svg width="80" height="80" viewBox="0 0 80 80" fill="none" stroke="#2a6b7a" stroke-width="2.5"><path d="M26 60c-8-5-12-13-12-22a20 20 0 0 1 40 0c0 9-4 17-12 22v8H26z"/><circle cx="52" cy="24" r="10"/><circle cx="36" cy="40" r="7"/><path d="M28 74h16M8 36H2M40 8V2M14 14l-5-5"/></svg>
    <div class="step-name">Innovative IP</div>
    <div class="step-line">Inventor Disclosure<br>Provisional Patent<br>Licensing agreement</div>
  </div>
  <div class="abs step-card" style="left:616px;top:1270px">
    <svg width="80" height="80" viewBox="0 0 80 80" fill="none" stroke="#2a6b7a" stroke-width="2.5"><circle cx="26" cy="26" r="12"/><circle cx="26" cy="26" r="5"/><path d="M44 14h16M44 26h20M44 38h12"/><circle cx="62" cy="14" r="3"/><circle cx="66" cy="26" r="3"/><path d="M6 62h14l14 6 30-12c4-2 2-8-3-7l-21 6H30M20 56l10-4h14"/></svg>
    <div class="step-name">Strategic Business Plan</div>
    <div class="step-line">Invention Assessment Voice of<br>Customer Product Business<br>Model/Plan Pitch Deck</div>
  </div>
  <div class="abs step-card" style="left:887px;top:1270px">
    <svg width="80" height="80" viewBox="0 0 80 80" fill="none" stroke="#2a6b7a" stroke-width="2.5"><path d="M12 10h44v10H12zM14 20v48h40M20 28h30v24H20zM26 46v-8M34 46V34M42 46v-6M50 56l12-6 14 6-14 6z"/></svg>
    <div class="step-name">Company Formation</div>
    <div class="step-line">Business model<br>Org structure &amp; planning<br>Cash planning</div>
  </div>

  <div class="abs knob" style="left:231px;top:1252px"></div><div class="abs knob" style="left:231px;top:1543px"></div>
  <div class="abs knob" style="left:503px;top:1252px"></div><div class="abs knob" style="left:503px;top:1543px"></div>
  <div class="abs knob" style="left:774px;top:1252px"></div><div class="abs knob" style="left:774px;top:1543px"></div>
  <div class="abs knob" style="left:1045px;top:1252px"></div><div class="abs knob" style="left:1045px;top:1543px"></div>
</section>

<section>
  <h2 class="abs h2 sol-title">The Solution</h2>
  <p class="abs sol-intro">K7 was started to solve significant problems associated with rapidly bringing innovative and transformational IP to market.</p>
  <p class="abs sol-sub">These costly problems include:</p>
  <div class="abs problem" style="top:1805px"><i></i><span>Incomplete strategic planning</span></div>
  <div class="abs problem" style="top:1841px"><i></i><span>Difficulty finding leadership</span></div>
  <div class="abs problem" style="top:1877px;width:360px"><i></i><span>Not able to differentiate a product or service from others that are already available</span></div>
  <div class="abs problem" style="top:1937px"><i></i><span>Ignoring the needs of customer</span></div>

  <div class="abs issue" style="left:498px;top:1691px">
    <svg width="90" height="90" viewBox="0 0 90 90" fill="none" stroke="#222" stroke-width="2.5"><circle cx="18" cy="12" r="6"/><circle cx="45" cy="12" r="6"/><circle cx="72" cy="12" r="6"/><path d="M8 50V24h20v26M35 50V24h20v26M62 50V24h20v26M12 50v30M24 50v30M39 50v30M51 50v30M66 50v14"/><circle cx="70" cy="70" r="14" stroke="#4fb3c8"/><path d="M70 62v14M64 71l6 6 6-6" stroke="#4fb3c8"/></svg>
    <span>Capital shortages</span>
  </div>
  <div class="abs issue" style="left:712px;top:1762px">
    <svg width="70" height="90" viewBox="0 0 70 90" fill="none" stroke="#222" stroke-width="2.5"><path d="M35 70C20 52 10 40 10 28a25 25 0 0 1 50 0c0 12-10 24-25 42z"/><circle cx="35" cy="28" r="10"/><ellipse cx="35" cy="78" rx="24" ry="7" stroke="#4fb3c8"/></svg>
    <span>Poor locations</span>
  </div>
  <div class="abs issue" style="left:927px;top:1691px">
    <svg width="90" height="90" viewBox="0 0 90 90" fill="none" stroke="#222" stroke-width="2.5"><path d="M20 30c-8 0-12 8-10 18 2 12 6 20 8 30 2 6 8 6 9 0l4-16c1-4 7-4 8 0l4 16c1 6 7 6 9 0 2-10 6-18 8-30 2-10-2-18-10-18-6 0-9 4-15 4s-9-4-15-4z"/><path d="M40 14l8 10M48 8l16 20M52 10l30-6" stroke="#4fb3c8"/></svg>
    <span>Scaling</span>
  </div>
</section>

<section>
  <div class="abs partners"></div>
  <h2 class="abs partners-title">Meet The Partners</h2>

  <svg class="abs" style="left:0;top:2100px" width="1200" height="380" viewBox="0 0 1200 380" fill="none">
    <g stroke-width="3">
      <circle cx="253" cy="181" r="163" stroke="#4fb3c8"/><circle cx="253" cy="181" r="144" stroke="#1f4a5c"/>
      <circle cx="600" cy="181" r="163" stroke="#4fb3c8"/><circle cx="600" cy="181" r="144" stroke="#1f4a5c"/>
      <circle cx="946" cy="181" r="163" stroke="#4fb3c8"/><circle cx="946" cy="181" r="144" stroke="#1f4a5c"/>
    </g>
    <g fill="#4fb3c8">
      <circle cx="386" cy="86" r="6"/><circle cx="101" cy="242" r="6"/>
      <circle cx="733" cy="86" r="6"/><circle cx="448" cy="242" r="6"/>
      <circle cx="1079" cy="86" r="6"/><circle cx="794" cy="242" r="6"/>
    </g>
    <g fill="#fff"><circle cx="309" cy="44" r="4"/><circle cx="656" cy="44" r="4"/><circle cx="1002" cy="44" r="4"/><circle cx="253" cy="325" r="4"/><circle cx="600" cy="325" r="4"/><circle cx="946" cy="325" r="4"/></g>
  </svg>
  <div class="abs partner-photo" style="left:115px;top:2143px;background:linear-gradient(160deg,#e9e6e1,#b9b2a8)" role="img" aria-label="Portrait of partner Mara Ellison in a striped blazer"></div>
  <div class="abs partner-photo" style="left:462px;top:2143px;background:linear-gradient(160deg,#6b5640,#2f3442)" role="img" aria-label="Portrait of partner RD Calloway holding a tablet"></div>
  <div class="abs partner-photo" style="left:808px;top:2143px;background:linear-gradient(160deg,#e6e7e8,#8f9a94)" role="img" aria-label="Portrait of partner LN Fairbank in a green blouse"></div>

  <div class="abs partner-name" style="left:103px;top:2465px">Mara Ellison</div>
  <div class="abs partner-name" style="left:450px;top:2465px">RD Calloway</div>
  <div class="abs partner-name" style="left:796px;top:2465px">LN Fairbank</div>
  <svg class="abs" style="left:0;top:2506px" width="1200" height="20" viewBox="0 0 1200 20">
    <g fill="#111"><circle cx="253" cy="10" r="9"/><circle cx="600" cy="10" r="9"/><circle cx="946" cy="10" r="9"/></g>
    <g stroke="#fff" stroke-width="2.2" fill="none"><path d="M249 8l4 4 4-4M596 8l4 4 4-4M942 8l4 4 4-4"/></g>
  </svg>
</section>

<section>
  <h2 class="abs funding-title">Funding</h2>
  <div class="abs fund fund-vc">
    <h3>Venture Capital</h3>
    <p>Angel<br>Private Equity</p>
  </div>
  <div class="abs fund fund-other">
    <h3>Other Sources</h3>
    <p>Grants (NIH/DOD)<br>Philanthropic<br>Industry<br>Institutional<br>Loans</p>
  </div>
</section>

<footer>
  <div class="abs site-footer"></div>
  <div class="abs foot-brand">The K7 Momentum Collective™</div>
  <nav class="abs foot-nav">
    <a>Home</a><a>About Us</a><a>Solution</a><a>Partners</a><a>Contact Us</a><a>Privacy Policy</a><a>Terms and Conditions</a>
  </nav>
  <span class="abs social" style="left:502px" aria-label="Social profile"></span>
  <span class="abs social" style="left:556px" aria-label="Social profile"></span>
  <span class="abs social" style="left:610px" aria-label="Social profile"></span>
  <span class="abs social" style="left:664px" aria-label="Social profile"></span>
  <p class="abs copyright">Copyrights@2023.The K7 Momentum Collective™.All Rights Reserved</p>
</footer>

</body>
</html>
```